packing for cake and sweet

we need packing design for cake box.
I attached some nice packing from other shop like :
Vira and belmonde for examples.

I attached the logo.
you can make packing with any colors you choose.

box size :
length : 30 cm
Width : 30 cm
Height : 15 cm

this shops have very good design :
https://www.brambleworth.example/hot-chocolate/discover-hot-chocolate/all-hot-chocolate

Industry/Entity Type

food

Font styles to use
Other font styles liked:
• same our logo already attached.

```html
<!DOCTYPE html>
<html lang="en">
<head>
<meta charset="utf-8">
<title>Vellance Cake Box Dieline</title>
<link rel="stylesheet" href="https://fonts.googleapis.com/css2?family=Cinzel:wght@400;500&display=swap">
<style>
  :root {
    --backdrop: #dfdbea;
    --lilac: #9e77b5;
    --plum: #3a2260;
    --crease: #a9b860;
    --ink: #3a2260;
    --wreath-ink: #5e3b8f;
    --blush: #f3e9f1;
  }
  html, body {
    margin: 0;
    padding: 0;
    width: 1015px;
    height: 1200px;
    overflow: hidden;
    background: var(--backdrop);
  }
  .dieline {
    display: block;
    width: 1015px;
    height: 1200px;
  }
  .panel-lilac { fill: var(--lilac); }
  .panel-plum { fill: var(--plum); }
  .cut { stroke: var(--crease); stroke-width: 0.6; }
  .crease { stroke: var(--crease); stroke-width: 0.6; fill: none; }
  .wordmark {
    font-family: "Cinzel", serif;
    font-weight: 400;
    fill: var(--ink);
    text-anchor: middle;
    dominant-baseline: middle;
  }
  .wordmark-wreath { fill: var(--wreath-ink); }
  .city {
    font-family: "Cinzel", serif;
    font-size: 3px;
    fill: var(--wreath-ink);
    text-anchor: middle;
    letter-spacing: 0.5px;
  }
  .shadowed { filter: drop-shadow(0 3px 4px rgba(60, 40, 90, 0.25)); }
</style>
</head>
<body>
<svg class="dieline" viewBox="0 0 1015 1200" xmlns="http://www.w3.org/2000/svg">
  <defs>
    <radialGradient id="wreath-floral" cx="50%" cy="50%" r="50%">
      <stop offset="0%" stop-color="#f6eef5"/>
      <stop offset="55%" stop-color="#efe3f0"/>
      <stop offset="78%" stop-color="#c6a4d8"/>
      <stop offset="100%" stop-color="#6f8f5a" stop-opacity="0.85"/>
    </radialGradient>
    <radialGradient id="wreath-leafy" cx="50%" cy="50%" r="50%">
      <stop offset="0%" stop-color="#efe3ee"/>
      <stop offset="50%" stop-color="#e6d6e8"/>
      <stop offset="75%" stop-color="#5f7f55"/>
      <stop offset="100%" stop-color="#3f5a3d" stop-opacity="0.7"/>
    </radialGradient>
  </defs>

  <g class="shadowed">
    <!-- top flaps row -->
    <rect class="panel-lilac cut" x="196" y="144" width="177" height="150"/>
    <rect class="panel-plum cut" x="373" y="144" width="269" height="150"/>
    <rect class="panel-lilac cut" x="642" y="144" width="176" height="150"/>

    <!-- side locking tabs -->
    <rect class="panel-plum" x="64" y="368" width="12" height="122"/>
    <rect class="panel-plum" x="939" y="368" width="11" height="122"/>

    <!-- middle row -->
    <rect class="panel-plum cut" x="73" y="294" width="150" height="269"/>
    <rect class="panel-plum cut" x="223" y="294" width="150" height="269"/>
    <rect class="panel-lilac cut" x="373" y="294" width="269" height="269"/>
    <rect class="panel-plum cut" x="642" y="294" width="150" height="269"/>
    <rect class="panel-plum cut" x="792" y="294" width="150" height="269"/>

    <!-- lower flaps row -->
    <rect class="panel-lilac cut" x="196" y="563" width="177" height="151"/>
    <rect class="panel-plum cut" x="373" y="563" width="269" height="151"/>
    <rect class="panel-lilac cut" x="642" y="563" width="176" height="151"/>

    <!-- lid dust flaps -->
    <path class="panel-lilac cut" d="M373 714 L304 741 Q281 752 281 770 V922 Q281 942 304 955 L373 982 Z"/>
    <path class="panel-lilac cut" d="M642 714 L711 741 Q733 752 733 770 V922 Q733 942 711 955 L642 982 Z"/>

    <!-- lid panel -->
    <rect class="panel-plum cut" x="373" y="714" width="269" height="268"/>

    <!-- tuck flap -->
    <path class="panel-lilac cut" d="M373 982 H642 V1001 Q642 1040 554 1058 V1066 Q554 1088 508 1088 Q461 1088 461 1066 V1058 Q373 1040 373 1001 Z"/>
  </g>

  <!-- slot and slits -->
  <line class="crease" x1="460" y1="220" x2="552" y2="220"/>
  <line class="crease" x1="236" y1="223" x2="236" y2="294"/>
  <line class="crease" x1="778" y1="223" x2="778" y2="294"/>
  <line class="crease" x1="236" y1="642" x2="236" y2="714"/>
  <line class="crease" x1="778" y1="642" x2="778" y2="714"/>

  <!-- base panel wordmark -->
  <text class="wordmark" x="507" y="429" font-size="27" transform="rotate(180 507 429)">Vellance</text>

  <!-- left side wreath -->
  <ellipse cx="301" cy="440" rx="50" ry="58" fill="url(#wreath-floral)" role="img" aria-label="Watercolour wreath of lilac roses and green leaves"/>
  <text class="wordmark wordmark-wreath" x="302" y="440" font-size="10" transform="rotate(-90 302 440)">Vellance</text>

  <!-- right side wreath -->
  <ellipse cx="721" cy="436" rx="50" ry="58" fill="url(#wreath-floral)" role="img" aria-label="Watercolour wreath of lilac roses and green leaves"/>
  <text class="wordmark wordmark-wreath" x="720" y="438" font-size="10" transform="rotate(90 720 438)">Vellance</text>

  <!-- front panel diamond wreath -->
  <ellipse cx="507" cy="638" rx="80" ry="52" fill="url(#wreath-leafy)" role="img" aria-label="Diamond frame with green foliage, a peach rose and a cream peony"/>
  <text class="wordmark wordmark-wreath" x="506" y="637" font-size="11" transform="rotate(180 506 637)">Vellance</text>

  <!-- lid main wreath -->
  <ellipse cx="504" cy="846" rx="114" ry="104" fill="url(#wreath-floral)" role="img" aria-label="Large watercolour wreath of lilac and pink roses with greenery around a white circle"/>
  <circle cx="506" cy="846" r="52" fill="var(--blush)"/>
  <circle cx="506" cy="834" r="3.5" fill="var(--wreath-ink)"/>
  <text class="wordmark wordmark-wreath" x="506" y="849" font-size="20">Vellance</text>
  <text class="city" x="506" y="859">BAKERY</text>

  <!-- tuck flap wordmark -->
  <text class="wordmark" x="507" y="1023" font-size="14">Vellance</text>
</svg>
</body>
</html>
```